Redesign of the UI of a customer service platform

To improve the user experience of our customers, we need a new design for our agent interface of our customer service platform (velorant.com).
The focus will be on the dashboard and the inbox screens (see attached) along with the common UI elements (Buttons, menu, fonts, forms...)
We want a simple and distinctive design

Target Market(s)

Worldwide

Industry/Entity Type

It Service

Number of Pages Required

3 page

Font styles to use
Sans Serif

Requirements
Must have
• New Onboarding page: this is a new page that is shown to user the first time they login to the platform. This will replace the current onboarding screen (setup SMS, Setup widget...etc)
• Dashboard page: to access important information and activate services (see screenshot from current site)
• Inbox page: to manage all the interactions with customers. (see screenshot from current site)
• UI elements (buttons, menus, forms, tables, fonts, color palette)

```html
<!DOCTYPE html>
<html lang="en">
<head>
<meta charset="utf-8">
<title>Velorant – Get Started</title>
<link href="https://fonts.googleapis.com/css2?family=Ubuntu:wght@300;400;500&display=swap" rel="stylesheet">
<style>
  :root{
    --brand:#f05228;
    --ink:#3c3c3c;
    --muted:#8d8d8d;
    --icon:#a9a9a9;
    --line:#e2e2e2;
    --panel:#f2f2f2;
    --white:#ffffff;
    --green:#3fb52d;
    --badge-red:#e8141c;
    --badge-yellow:#f7b500;
  }
  *{box-sizing:border-box;margin:0;padding:0}
  html,body{width:1200px;height:1062px;overflow:hidden;background:var(--white);font-family:"Ubuntu",sans-serif;color:var(--ink)}
  .app{position:relative;width:1200px;height:1062px;overflow:hidden}

  /* top navigation */
  .topbar{position:absolute;left:0;top:0;width:1200px;height:83px;background:var(--white);display:flex}
  .brand{width:83px;height:83px;background:var(--brand);color:var(--white);display:flex;align-items:center;justify-content:center;font-size:15px;font-weight:400}
  .nav{display:flex}
  .nav-item{position:relative;width:84px;height:83px;border-right:1px solid #ececec;display:flex;flex-direction:column;align-items:center;justify-content:flex-start;padding-top:15px;color:var(--muted);font-size:13px;font-weight:300}
  .nav-item svg{width:28px;height:28px;margin-bottom:8px}
  .count{position:absolute;top:17px;left:50px;width:22px;height:22px;border-radius:50%;color:var(--white);font-size:12px;display:flex;align-items:center;justify-content:center;font-weight:400}
  .count.red{background:var(--badge-red)}
  .count.yellow{background:var(--badge-yellow)}
  .user{position:absolute;right:14px;top:14px;width:55px;height:55px}
  .user .photo{width:55px;height:55px;border-radius:50%;background:radial-gradient(circle at 50% 40%,#d9b49a,#6b5445 70%,#e8e8e8 72%)}
  .user .online{position:absolute;left:-2px;top:0;width:14px;height:14px;border-radius:50%;background:var(--green)}

  /* onboarding panel */
  .onboard{position:absolute;left:0;top:83px;width:1200px;height:679px;background:var(--panel)}
  .title{position:absolute;left:0;width:1200px;text-align:center;font-weight:400}
  .title.main{top:31px;font-size:27px}
  .video{position:absolute;left:344px;top:94px;width:512px;height:299px;background:linear-gradient(120deg,#8a7468 0%,#d9b89b 35%,#c9a98e 55%,#6a4a3b 100%)}
  .play{position:absolute;left:222px;top:115px;width:70px;height:70px;border-radius:50%;background:rgba(255,255,255,.85);display:flex;align-items:center;justify-content:center}
  .player{position:absolute;left:344px;top:408px;width:512px;height:16px;display:flex;align-items:center;font-size:11px;color:var(--icon)}
  .player .time{margin:0 10px 0 8px}
  .track{flex:1;height:3px;background:#dcdcdc;position:relative}
  .track span{position:absolute;left:0;top:0;height:3px;width:50%;background:var(--brand)}
  .title.addons{top:461px;font-size:20px}
  .cards{position:absolute;left:182px;top:507px;display:flex;gap:19px}
  .card{position:relative;width:152px;height:153px;background:var(--white);border:1px solid var(--line);text-align:center}
  .card .ring{width:65px;height:65px;border-radius:50%;border:1px solid var(--line);margin:19px auto 0;display:flex;align-items:center;justify-content:center}
  .card .ring svg{width:28px;height:28px}
  .card h3{font-size:17px;font-weight:400;margin-top:14px}
  .card a{display:block;font-size:11px;color:var(--brand);text-decoration:none;margin-top:6px;letter-spacing:.2px}
  .card .check{position:absolute;left:10px;top:9px;width:20px;height:20px}

  /* plan */
  .plan-head{position:absolute;left:0;top:802px;width:1200px;display:flex;justify-content:center;align-items:center;gap:8px}
  .plan-head h2{font-size:21px;font-weight:400}
  .tag{background:var(--brand);color:var(--white);font-size:11px;padding:2px 6px 3px;border-radius:2px;position:relative;top:-3px}
  .trial{position:absolute;left:0;top:836px;width:1200px;text-align:center;font-size:14px;color:var(--muted);font-weight:300}
  .limits{position:absolute;left:307px;top:886px;display:flex;border:1px solid var(--line)}
  .limit{position:relative;width:195px;height:68px;display:flex;align-items:center;padding-left:18px;gap:14px}
  .limit + .limit{border-left:1px solid var(--line)}
  .limit svg{width:34px;height:34px}
  .limit h4{font-size:16px;font-weight:400}
  .limit p{font-size:12px;color:var(--muted);font-weight:300;margin-top:3px}
  .quota{position:absolute;right:10px;top:-11px;background:var(--brand);color:var(--white);font-size:10px;padding:2px 8px;border-radius:2px}
  .quota::after{content:"";position:absolute;left:50%;bottom:-4px;margin-left:-4px;border:4px solid transparent;border-bottom:0;border-top-color:var(--brand)}
  .buy{position:absolute;left:558px;top:983px;width:84px;height:28px;background:var(--green);color:var(--white);font-size:12px;border:0;font-family:inherit;display:flex;align-items:center;justify-content:center}
</style>
</head>
<body>
<div class="app">
  <header class="topbar">
    <div class="brand">Velorant</div>
    <nav class="nav">
      <div class="nav-item">
        <svg viewBox="0 0 28 28" fill="#a9a9a9"><path d="M3 15h6l2 3h6l2-3h6v9H3z"/><path d="M12 4h4v6h3l-5 5-5-5h3z"/></svg>
        Inbox<span class="count red">4</span>
      </div>
      <div class="nav-item">
        <svg viewBox="0 0 28 28" fill="none" stroke="#a9a9a9" stroke-width="2"><rect x="5" y="4" width="16" height="20"/><path d="M9 10h8M9 14h8M9 18h5"/></svg>
        Tasks<span class="count yellow">1</span>
      </div>
      <div class="nav-item">
        <svg viewBox="0 0 28 28" fill="#a9a9a9"><circle cx="14" cy="9" r="5"/><path d="M4 25c0-6 4-9 10-9s10 3 10 9z"/></svg>
        Customers
      </div>
      <div class="nav-item">
        <svg viewBox="0 0 28 28" fill="none" stroke="#a9a9a9" stroke-width="2" stroke-linejoin="round"><path d="M3 5l22 9-22 9 4-9z M7 14h18"/></svg>
        Campaigns
      </div>
      <div class="nav-item">
        <svg viewBox="0 0 28 28" fill="none" stroke="#a9a9a9" stroke-width="2"><path d="M19 9c-1-2-3-3-5-3-3 0-5 1.5-5 4s3 3 5 3.5 5 1.5 5 4-2 4-5 4c-2.5 0-4.5-1-5.5-3M14 3v22"/></svg>
        Payments
      </div>
      <div class="nav-item">
        <svg viewBox="0 0 28 28" fill="#a9a9a9"><rect x="4" y="6" width="2.5" height="18"/><rect x="10" y="12" width="2.5" height="12"/><rect x="16" y="4" width="2.5" height="20"/><rect x="22" y="10" width="2.5" height="14"/></svg>
        Reports
      </div>
      <div class="nav-item">
        <svg viewBox="0 0 28 28" fill="#a9a9a9"><circle cx="14" cy="14" r="8"/><g stroke="#a9a9a9" stroke-width="4"><path d="M14 3v22M3 14h22M6 6l16 16M22 6L6 22"/></g><circle cx="14" cy="14" r="3" fill="#fff"/></svg>
        Settings
      </div>
    </nav>
    <div class="user">
      <div class="photo" role="img" aria-label="Agent profile photo"></div>
      <span class="online"></span>
    </div>
  </header>

  <main class="onboard">
    <h1 class="title main">Get Started</h1>
    <div class="video" role="img" aria-label="Video still of colleagues working at a desk with notes and a tablet">
      <div class="play"><svg width="22" height="22" viewBox="0 0 22 22"><path d="M5 2l15 9-15 9z" fill="#f05228"/></svg></div>
    </div>
    <div class="player">
      <svg width="10" height="10" viewBox="0 0 10 10"><path d="M1 0l8 5-8 5z" fill="#a9a9a9"/></svg>
      <span class="time">0:00</span>
      <div class="track"><span></span></div>
    </div>

    <h2 class="title addons">Select Your Add-ons</h2>
    <div class="cards">
      <div class="card">
        <div class="ring"><svg viewBox="0 0 28 28" fill="#a9a9a9"><rect x="3" y="5" width="22" height="14" rx="1"/><rect x="6" y="8" width="16" height="8" fill="#fff"/><rect x="12" y="19" width="4" height="3"/><rect x="8" y="22" width="12" height="2"/></svg></div>
        <h3>Campaigns</h3><a href="#">WATCH VIDEO</a>
      </div>
      <div class="card">
        <div class="ring"></div>
        <h3>ChatLink</h3><a href="#">WATCH VIDEO</a>
      </div>
      <div class="card">
        <svg class="check" viewBox="0 0 20 20"><circle cx="10" cy="10" r="10" fill="#3fb52d"/><path d="M5.5 10.5l3 3 6-6.5" fill="none" stroke="#fff" stroke-width="2.2"/></svg>
        <div class="ring"><svg viewBox="0 0 28 28"><path d="M14 4C8 4 3 8 3 13c0 3 1.5 5 4 7l-1 4 5-2.5c1 .3 2 .5 3 .5 6 0 11-4 11-9S20 4 14 4z" fill="#a9a9a9"/><path d="M9 11h10M9 14h10M9 17h6" stroke="#fff" stroke-width="1.5"/></svg></div>
        <h3>SMS</h3><a href="#">WATCH VIDEO</a>
      </div>
      <div class="card">
        <div class="ring"></div>
        <h3>Relaygram</h3><a href="#">WATCH VIDEO</a>
      </div>
      <div class="card">
        <div class="ring"><svg viewBox="0 0 28 28" fill="none" stroke="#a9a9a9" stroke-width="2.6"><path d="M19 9c-1-2-3-3-5-3-3 0-5 1.5-5 4s3 3 5 3.5 5 1.5 5 4-2 4-5 4c-2.5 0-4.5-1-5.5-3M14 2v24"/></svg></div>
        <h3>Payment</h3><a href="#">WATCH VIDEO</a>
      </div>
    </div>
  </main>

  <div class="plan-head"><h2>Plan</h2><span class="tag">FREE</span></div>
  <p class="trial">Your trial period ends in 14 days</p>
  <div class="limits">
    <div class="limit">
      <svg viewBox="0 0 34 34" fill="#b0b0b0"><circle cx="17" cy="11" r="5"/><circle cx="8" cy="13" r="4"/><circle cx="26" cy="13" r="4"/><path d="M9 28c0-6 3-10 8-10s8 4 8 10z"/><path d="M1 26c0-5 3-8 7-8 1 0 2 .2 3 .6-2 2-3 4.5-3 7.4zM33 26c0-5-3-8-7-8-1 0-2 .2-3 .6 2 2 3 4.5 3 7.4z"/></svg>
      <div><h4>Agents</h4><p>Up to 3</p></div><span class="quota">1/3</span>
    </div>
    <div class="limit">
      <svg viewBox="0 0 34 34" fill="#b0b0b0"><path d="M12 8V6h10v2h-2V7.5h-6V8z"/><rect x="2" y="9" width="30" height="20" rx="2"/><rect x="2" y="18" width="30" height="1.5" fill="#fff"/><rect x="15" y="16" width="4" height="5" fill="#fff"/></svg>
      <div><h4>Departments</h4><p>Up to 3</p></div><span class="quota">1/3</span>
    </div>
    <div class="limit">
      <svg viewBox="0 0 34 34" fill="#b0b0b0"><path d="M7 3l5 6-3 3c2 5 6 9 11 11l3-3 6 5-4 5C14 29 5 20 3 7z"/></svg>
      <div><h4>Phones</h4><p>Up to 1</p></div><span class="quota">1/3</span>
    </div>
  </div>
  <button class="buy">BUY NOW</button>
</div>
</body>
</html>
```